Velk Partners Building Business Cards

We need a business card that reflects our business as "Solar Experts" in San Diego. Browse our website www.velkpartners.example our License needs to be displayed as "CSLB# 3867140" our phone number is (619) 555-0187

Save thousands on your electric bills and increase the value of your home while helping to protect the environment. Our solar installation experts will help you design the system that's right for you, using only the highest quality equipment that will look great and give you ideal performance. Our goal is to make you energy independent, and get your electric bill to 0.

Paul Osterby
(619) 555-0187
paul@velkpartners.example

Target Market(s)

Home owners in san diego looking for solar

Industry/Entity Type

Solar Energy

Contact Information for Business Card

Paul Osterby
(619) 555-0187
paul@velkpartners.example

Font styles to use
Other font styles liked:
• Use our logo font

Requirements
Must have
• License needs to be displayed as "CSLB# 3867140" our phone number is (619) 555-0187
Nice to have
• Real images of rooftop home solar in san diego
Should not have
• our business address

```html
<!DOCTYPE html>
<html lang="en">
<head>
<meta charset="utf-8">
<title>Velk Partners Building – Business Card</title>
<link rel="stylesheet" href="https://fonts.googleapis.com/css2?family=Open+Sans:ital,wght@0,400;0,600;0,700;1,400&display=swap">
<style>
  :root {
    --navy: #1d4284;
    --navy-dark: #163569;
    --sun: #f4b41a;
    --paper: #ffffff;
    --ink-grey: #555a62;
    --rule: #c9ccd2;
    --backdrop: #e9e7e2;
  }
  * { box-sizing: border-box; margin: 0; padding: 0; }
  html, body { width: 1200px; height: 950px; overflow: hidden; }
  body {
    background: var(--backdrop);
    font-family: "Open Sans", Arial, sans-serif;
    position: relative;
  }
  .card {
    position: absolute;
    width: 660px;
    height: 378px;
    left: 270px;
    box-shadow: 0 10px 26px rgba(0,0,0,.18);
    overflow: hidden;
  }
  .card--front { top: 70px; background: var(--paper); }
  .card--back { top: 502px; background: var(--navy); }

  .front-band { position: absolute; left: 0; bottom: 0; width: 100%; height: 80px; }

  .brand-name {
    position: absolute;
    left: 60px; top: 92px;
    font-size: 40px; font-weight: 700;
    color: var(--navy);
    letter-spacing: -0.5px;
    display: flex; align-items: center; gap: 14px;
  }
  .brand-dot { width: 22px; height: 22px; border-radius: 50%; background: var(--sun); flex: none; }

  .person { position: absolute; left: 60px; top: 196px; }
  .person-name { font-size: 24px; font-weight: 700; color: var(--navy); }
  .person-role { font-size: 16px; color: var(--sun); margin-top: 2px; }
  .person-license { font-size: 16px; color: var(--ink-grey); margin-top: 2px; }

  .divider { position: absolute; left: 318px; top: 190px; width: 1px; height: 96px; background: var(--rule); }

  .contact { position: absolute; left: 340px; top: 196px; list-style: none; }
  .contact li {
    display: flex; align-items: center; gap: 10px;
    font-size: 15px; color: var(--ink-grey); line-height: 28px;
  }
  .contact svg { width: 14px; height: 14px; flex: none; }

  .back-footer {
    position: absolute;
    left: 40px; right: 40px; bottom: 40px;
    display: flex; align-items: center; justify-content: space-between;
  }
  .back-web {
    font-size: 14px; color: #ffffff; font-style: italic;
  }
  .back-brand {
    font-size: 22px; font-weight: 700; color: #ffffff;
    display: flex; align-items: center; gap: 10px;
  }
  .back-brand .brand-dot { width: 16px; height: 16px; }
</style>
</head>
<body>

<section class="card card--front" aria-label="Business card front">
  <svg class="front-band" viewBox="0 0 660 80" preserveAspectRatio="none" aria-hidden="true">
    <polygon points="0,48 520,48 540,22 560,48 660,48 660,80 0,80" fill="var(--sun)"/>
    <polygon points="0,53 520,53 540,28 560,53 660,53 660,80 0,80" fill="var(--navy)"/>
  </svg>

  <div class="brand-name"><span>Velk Partners Building</span><span class="brand-dot"></span></div>

  <div class="person">
    <p class="person-name">Paul Osterby</p>
    <p class="person-role">CEO/Founder</p>
    <p class="person-license">CSLB# 3867140</p>
  </div>

  <div class="divider"></div>

  <ul class="contact">
    <li>
      <svg viewBox="0 0 16 16" aria-hidden="true"><path fill="var(--navy)" d="M3.6 1.5l2.2 2.7-1.3 1.6c.9 2 2.6 3.7 4.6 4.6l1.6-1.3 2.7 2.2-1.4 2.2C6.6 13.2 2.8 9.4 1.4 2.9z"/></svg>
      (619) 555-0187
    </li>
    <li>
      <svg viewBox="0 0 16 16" aria-hidden="true"><rect x="1" y="3" width="14" height="10" rx="1" fill="var(--navy)"/><path d="M1.5 3.5L8 9l6.5-5.5" stroke="#fff" stroke-width="1.4" fill="none"/></svg>
      paul@velkpartners.example
    </li>
    <li>
      <svg viewBox="0 0 16 16" aria-hidden="true"><circle cx="8" cy="8" r="7" fill="var(--navy)"/><path d="M1 8h14M8 1c3 3 3 11 0 14M8 1c-3 3-3 11 0 14" stroke="#fff" stroke-width="1" fill="none"/></svg>
      www.velkpartners.example
    </li>
  </ul>
</section>

<section class="card card--back" aria-label="Business card back">
  <div class="back-footer">
    <p class="back-web">www.velkpartners.example</p>
    <div class="back-brand"><span class="brand-dot"></span><span>Velk Partners Building</span></div>
  </div>
</section>

</body>
</html>
```